Strategy and Technology Consulting - Our Story and Values Page

Interior Page design – Our History and Our Values

Our homepage has been designed and we are looking for a design for one of the interior pages. This interior page tells the story of Our History and Our Values

Because the homepage has been designed, we would like this interior page to reflect the design of the homepage without being a mirror image of the homepage.

This site will be implemented in WordPress using the Elementor framework.

Font: Poppins medium and Poppins dark
Illustrations: Our homepage illustrations were designed by “Brelin 1974” on Quillmark. Compatible original or stock illustrations are welcome. Stock photography is also welcome. Brelin is also available through Brelin Tosamek on Ravolo

Uploaded Files
• Homepage design – this is the design we will use for our homepage. Contest entries should reflect this basic style but should be distinctly different from the homepage.
• Our History and Our Values – Wireframe – the basic layout of the page we are looking for.
• Our History and Our Values – Word document with the text supporting the wireframe.
• Color Palette – please use colors compatible with the palette attached.

Our Story - timeline
There is a timeline element in the wireframe. The wireframe displays this as a series of chevrons (arrows), but it does not need to be. Creativity in display of the timeline is appreciated.

Our Values
If you look at the Word document, you will see that there are a lot of words on the page. The winning design will present the information in a way that engages the user without overwhelming them with too much to read. For example, they may click on a value and see more information.

Target Market(s)

CIO's and Technology Executives

Number of Pages Required

1 page

Font styles to use
Sans Serif
Other font styles liked:
• Poppin

Requirements
Must have
• A timeline element, all of our values
Nice to have
• Clever timeline display

```html
<!DOCTYPE html>
<html lang="en">
<head>
<meta charset="utf-8">
<title>Corvane – Our Story and Values</title>
<link href="https://fonts.googleapis.com/css2?family=Poppins:wght@300;400;500;600;700;800&family=Montserrat:wght@500;600&family=Nunito+Sans:wght@400;600&display=swap" rel="stylesheet">
<style>
  :root{
    --navy:#2a5e8c;
    --sky:#b9d9f0;
    --slate:#a4b5c3;
    --gold:#f0b323;
    --gold-soft:#d9a93a;
    --ink:#2f2f2f;
    --body:#4a4a4a;
    --muted:#8a8f96;
    --line:#7a7a7a;
    --footer:#46556b;
    --footer-dark:#3a4659;
    --white:#ffffff;
  }
  *{box-sizing:border-box;margin:0;padding:0}
  html,body{width:1200px;height:3930px;overflow:hidden}
  body{position:relative;background:var(--white);font-family:'Poppins',sans-serif;color:var(--ink)}
  .abs{position:absolute}

  /* header */
  .site-header{position:absolute;left:0;top:0;width:1200px;height:88px;border-bottom:1px solid #eceff2}
  .brand{position:absolute;display:flex;align-items:center;gap:8px;font-family:'Poppins',sans-serif;font-weight:400;color:var(--muted)}
  .brand-dot{width:12px;height:12px;border-radius:50%;background:var(--navy)}
  .site-header .brand{left:110px;top:18px;font-size:44px;line-height:52px}
  .main-nav{position:absolute;left:545px;top:34px;display:flex;gap:22px;align-items:center;font-size:12.5px;font-weight:600;color:#3b4350;letter-spacing:.2px}
  .main-nav .home{width:14px;height:13px;background:#9aa5b2;clip-path:polygon(50% 0,100% 45%,85% 45%,85% 100%,15% 100%,15% 45%,0 45%)}
  .main-nav span.caret::after{content:" ⌄";font-size:11px}
  .btn-gold{position:absolute;display:flex;align-items:center;justify-content:center;background:var(--gold);color:var(--white);font-weight:700;font-size:11.5px;border-radius:30px;letter-spacing:.3px}
  .site-header .btn-gold{left:967px;top:25px;width:126px;height:37px}

  /* timeline */
  .phase-tag{position:absolute;top:194px;width:226px;height:50px}
  .phase-tag svg{position:absolute;inset:0}
  .phase-tag span{position:absolute;inset:0;display:flex;align-items:center;justify-content:center;color:var(--white);font-weight:500;font-size:17px;padding-left:12px}
  .phase-stem{position:absolute;top:244px;width:2px;height:62px;background:var(--line)}
  .phase-ring{position:absolute;top:304px;width:160px;height:160px;border:3px solid var(--line);border-radius:50%;display:flex;align-items:center;justify-content:center}
  .phase-ring .art{width:80px;height:80px;border-radius:50%;background:linear-gradient(135deg,#f4d38a,#f0b323)}
  .phase-list{position:absolute;top:488px;list-style:none;font-size:14px;line-height:21px;color:#3c3c3c}
  .phase-list li{position:relative;padding-left:21px;margin-bottom:7px}
  .phase-list li::before{content:"";position:absolute;left:0;top:5px;width:10px;height:10px;border:2.5px solid var(--gold);border-radius:50%}
  .phase-list li.plain{padding-left:21px}
  .phase-list li.plain::before{display:none}

  /* value cards */
  .value-card{position:absolute;left:215px;width:770px;height:284px;background:var(--white);border-radius:14px;box-shadow:0 2px 14px rgba(0,0,0,.09)}
  .value-card .divider{position:absolute;top:35px;width:2px;height:212px;background:var(--navy)}
  .value-card .art{position:absolute;top:82px;width:130px;height:120px;border-radius:12px;background:linear-gradient(135deg,#5f7f9e,#d4aa4a)}
  .value-card h2{position:absolute;top:32px;font-family:'Montserrat',sans-serif;font-weight:500;font-size:24px;color:#262626}
  .value-card p{position:absolute;top:92px;width:492px;font-family:'Nunito Sans',sans-serif;font-size:15.5px;line-height:26.6px;color:var(--body);text-align:justify}
  .learn{position:absolute;font-family:'Montserrat',sans-serif;font-weight:500;font-size:16px;color:var(--gold);display:flex;align-items:center;gap:5px}
  .learn i{width:14px;height:14px;border-radius:50%;background:var(--gold);position:relative}
  .learn i::after{content:"";position:absolute;left:4px;top:4px;width:4px;height:4px;border-top:2px solid #fff;border-right:2px solid #fff;transform:rotate(45deg)}
  .art-left .divider{left:207px}
  .art-left .art{left:45px}
  .art-left h2,.art-left p{left:249px}
  .art-left .learn{left:249px;bottom:34px}
  .art-right .divider{left:563px}
  .art-right .art{left:604px}
  .art-right h2{right:250px;text-align:right}
  .art-right p{left:29px}
  .art-right .learn{right:250px;bottom:34px}

  /* newsletter + footer */
  .footer-wave{position:absolute;left:0;top:3160px;width:1200px;height:770px}
  .newsletter{position:absolute;left:134px;top:3212px;width:930px;height:207px;border-radius:104px;background:var(--gold);background-image:radial-gradient(rgba(255,255,255,.18) 1px,transparent 1px);background-size:6px 6px}
  .newsletter h3{position:absolute;left:80px;top:56px;font-weight:800;font-size:33px;color:var(--white)}
  .newsletter p{position:absolute;left:81px;top:110px;width:430px;font-weight:500;font-size:15px;line-height:20px;color:var(--white)}
  .subscribe{position:absolute;left:554px;top:82px;width:322px;height:46px;background:var(--white);border-radius:23px;display:flex;align-items:center;padding-left:24px;gap:9px;font-size:12.5px;color:#8a8f96}
  .subscribe .env{width:13px;height:9px;background:#9aa5b2;border-radius:1px}
  .subscribe .send{position:absolute;right:5px;top:5px;width:36px;height:36px;border-radius:50%;background:#8e9fb3}
  .subscribe .send::after{content:"";position:absolute;left:11px;top:12px;border-left:14px solid #fff;border-top:6px solid transparent;border-bottom:6px solid transparent;transform:rotate(-35deg)}
  .footer-brand{left:116px;top:3602px;font-size:64px;line-height:70px;color:#c9cfd7}
  .footer-brand .brand-dot{background:var(--gold);width:14px;height:14px}
  .social{position:absolute;top:3679px;left:172px;display:flex;gap:8px}
  .social span{width:43px;height:43px;border-radius:50%;background:rgba(255,255,255,.18)}
  .footer .btn-gold{left:210px;top:3744px;width:133px;height:38px}
  .footer-col{position:absolute;top:3580px;color:var(--white)}
  .footer-col h4{font-weight:700;font-size:20px;margin-bottom:18px}
  .footer-col ul{list-style:none;font-size:12.5px;color:#e6e9ee}
  .footer-col li{height:31px;padding-left:14px;position:relative}
  .footer-col li::before{content:"›";position:absolute;left:0;top:-2px;font-size:15px}
  .contact-item{position:relative;padding-left:22px;font-size:12.5px;line-height:17px;color:#e6e9ee;margin-bottom:17px}
  .contact-item::before{content:"";position:absolute;left:0;top:3px;width:12px;height:10px;background:var(--gold);border-radius:2px}
  .contact-item.pin::before{border-radius:50% 50% 50% 0;transform:rotate(-45deg);width:10px;height:10px}
  .legal{position:absolute;left:0;top:3866px;width:1200px;height:64px;background:var(--footer-dark);display:flex;align-items:center;justify-content:center;font-size:13px;font-weight:500;color:var(--white)}
  .chat{position:absolute;left:1139px;top:3842px;width:48px;height:48px;border-radius:50%;background:var(--gold)}
  .chat::after{content:"";position:absolute;left:13px;top:14px;width:22px;height:17px;border-radius:50%;background:#fff}
</style>
</head>
<body>

<header class="site-header">
  <div class="brand"><span class="brand-dot"></span>Corvane</div>
  <nav class="main-nav">
    <span class="home"></span>
    <span class="caret">ABOUT US</span>
    <span class="caret">SERVICES</span>
    <span class="caret">INSIGHTS</span>
    <span class="caret">JOIN US</span>
  </nav>
  <a class="btn-gold">CONTACT US</a>
</header>

<section class="timeline">
  <div class="phase-tag" style="left:148px">
    <svg viewBox="0 0 226 50"><polygon points="0,0 205,0 226,25 205,50 0,50 21,25" fill="#2a5e8c"/></svg>
    <span>2017 – 2019</span>
  </div>
  <div class="phase-stem" style="left:255px"></div>
  <div class="phase-ring" style="left:176px"><div class="art" role="img" aria-label="Growth chart with dollar coin icon"></div></div>
  <ul class="phase-list" style="left:161px">
    <li>Growth Strategy Focus</li>
    <li>Consistent, Modest Growth</li>
    <li>Preliminary Focus on Technology</li>
    <li>Eureka!&nbsp; Implementing strategy is hard.</li>
  </ul>

  <div class="phase-tag" style="left:480px">
    <svg viewBox="0 0 226 50"><polygon points="0,0 205,0 226,25 205,50 0,50 21,25" fill="#b9d9f0"/></svg>
    <span>2020 – 2021</span>
  </div>
  <div class="phase-stem" style="left:588px"></div>
  <div class="phase-ring" style="left:509px"><div class="art" role="img" aria-label="Business model and gear icon"></div></div>
  <ul class="phase-list" style="left:505px">
    <li>Pandemic Pauses Growth</li>
    <li>Rethinking</li>
    <li class="plain" style="margin-bottom:3px">the business model</li>
    <li class="plain">the delivery model</li>
  </ul>

  <div class="phase-tag" style="left:813px">
    <svg viewBox="0 0 226 50"><polygon points="0,0 205,0 226,25 205,50 0,50 21,25" fill="#a4b5c3"/></svg>
    <span>2022 and Onward</span>
  </div>
  <div class="phase-stem" style="left:920px"></div>
  <div class="phase-ring" style="left:841px"><div class="art" role="img" aria-label="Leadership team network icon"></div></div>
  <ul class="phase-list" style="left:825px;width:240px">
    <li>Leadership Team for Focus on Essential Areas</li>
    <li>Rapid Growth</li>
    <li>Customer Success</li>
  </ul>
</section>

<section class="values">
  <article class="value-card art-left" style="top:759px">
    <div class="art" role="img" aria-label="Hand holding dollar coins icon"></div>
    <div class="divider"></div>
    <h2>The Value of Every Human.&nbsp; Regardless</h2>
    <p>Each person's unique experiences and perspectives add vibrant hues to the tapestry of our shared existence.&nbsp; In a world where diversity paints the canvas of humanity, true beauty is found in recognizing the inherent and incalculable value of every human being.</p>
    <a class="learn">Learn More <i></i></a>
  </article>

  <article class="value-card art-right" style="top:1093px">
    <div class="art" role="img" aria-label="Four joined hands icon"></div>
    <div class="divider"></div>
    <h2>Collaboration</h2>
    <p style="text-align:justify;text-align-last:right">Collaboration in work transforms individual endeavors into symphonies of collective achievement. Through collaboration, diverse talents converge, fostering a rich exchange of ideas that amplifies creativity, accelerates progress, and brings forth solutions beyond what a single mind could conceive.</p>
    <a class="learn">Learn More <i></i></a>
  </article>

  <article class="value-card art-left" style="top:1427px">
    <div class="art" role="img" aria-label="Heart inside a flame icon"></div>
    <div class="divider"></div>
    <h2>Passion</h2>
    <p style="top:84px">Passion infuses our work with energy, transforming routine tasks into opportunities for creativity and innovation. Fueled by passion, individuals become unstoppable forces, driven to overcome challenges and achieve remarkable outcomes that benefit them and inspire those around them</p>
    <a class="learn">Learn More <i></i></a>
  </article>

  <article class="value-card art-right" style="top:1761px">
    <div class="art" role="img" aria-label="Person with growth chart and gear icon"></div>
    <div class="divider"></div>
    <h2>Excellence</h2>
    <p style="top:92px;text-align-last:right">Excellence isn't a destination; it's a continuous journey of refinement and growth. Striving for excellence cultivates a culture of continuous improvement, fostering innovation, credibility, and a lasting impact that resonates far beyond the immediate task.</p>
    <a class="learn">Learn More <i></i></a>
  </article>

  <article class="value-card art-left" style="top:2089px">
    <div class="art" role="img" aria-label="Raised fist icon"></div>
    <div class="divider"></div>
    <h2>Tenacity</h2>
    <p>Tenacity is the unwavering anchor that keeps us grounded amidst adversity, propelling us forward when faced with obstacles. The resilience to persist, adapt, and learn from setbacks leads to the mastery of skills and the fulfillment of ambitious goals.</p>
    <a class="learn">Learn More <i></i></a>
  </article>

  <article class="value-card art-right" style="top:2423px">
    <div class="art" role="img" aria-label="Thinking person with gears icon"></div>
    <div class="divider"></div>
    <h2>Solution Mindset</h2>
    <p style="top:84px;text-align-last:right">A solution mindset is the compass that directs our focus from problems to possibilities. It empowers us to navigate challenges with a proactive mindset, igniting a journey of exploration and innovation that not only resolves issues but also paves the way for continuous growth and success.</p>
    <a class="learn">Learn More <i></i></a>
  </article>

  <article class="value-card art-left" style="top:2757px">
    <div class="art" role="img" aria-label="Hand offering hearts icon"></div>
    <div class="divider"></div>
    <h2>Generosity</h2>
    <p style="top:84px">Generosity creates a virtuous cycle of goodwill, fostering a sense of unity and shared purpose among colleagues. By freely sharing knowledge, support, and resources, we uplift those around us and contribute to a collaborative environment where collective achievements flourish.</p>
    <a class="learn">Learn More <i></i></a>
  </article>
</section>

<footer class="footer">
  <svg class="footer-wave" viewBox="0 0 1200 770" preserveAspectRatio="none">
    <defs>
      <linearGradient id="waveFill" x1="0" y1="0" x2="0" y2="1">
        <stop offset="0" stop-color="#4a5a72"/>
        <stop offset="1" stop-color="#56687f"/>
      </linearGradient>
    </defs>
    <path d="M0,80 C120,40 220,150 330,240 C430,320 520,300 600,250 C700,185 800,180 900,220 C1000,260 1100,230 1200,170 L1200,770 L0,770 Z" fill="#d6dae0"/>
    <path d="M0,90 C130,50 230,170 340,260 C440,335 530,320 610,265 C710,200 810,195 910,235 C1010,275 1110,245 1200,185 L1200,770 L0,770 Z" fill="url(#waveFill)"/>
  </svg>

  <div class="newsletter">
    <h3>Subscribe Our Newsletter</h3>
    <p>Subscribe our newsletter to receive the latest news and exclusive offers every week, No spam.</p>
    <div class="subscribe"><span class="env"></span>Enter email address<span class="send"></span></div>
  </div>

  <div class="brand footer-brand"><span class="brand-dot"></span>Corvane</div>
  <div class="social"><span></span><span></span><span></span><span></span></div>
  <a class="btn-gold">CONTACT US</a>

  <div class="footer-col" style="left:490px">
    <h4>Quick links</h4>
    <ul><li>Home</li><li>About Us</li><li>Services</li><li>Insights</li><li>Join Us</li><li>Contact Us</li></ul>
  </div>
  <div class="footer-col" style="left:668px">
    <h4>Our Services</h4>
    <ul><li>Business Transformation</li><li>ERP Implementations</li><li>ERP Solutions</li><li>BI and Data</li><li>Building the Right Team...</li></ul>
  </div>
  <div class="footer-col" style="left:901px;width:200px">
    <h4>Contact info</h4>
    <div class="contact-item">Email:<br>hello@corvanemail.com</div>
    <div class="contact-item">Phone:<br>+44 113 555 0142</div>
    <div class="contact-item pin">Location:<br>Some address line goes here city name</div>
  </div>

  <div class="legal">© Corvane Design 2023, All Rights Reserved</div>
  <div class="chat"></div>
</footer>

</body>
</html>
```